Sparrow Haulage needs a business card design.

Design a double-sided business card for new freight business. On the front, would like to see our logo along with the following info:

Martin Obuya
CEO/FOUNDER
555-206-7142
martinobuya@sparrow-haulage.example

On the reverse side, we would like to use the graphic image of our logo only without the Sparrow Haulage name.

```html
<!DOCTYPE html>
<html lang="en">
<head>
<meta charset="utf-8">
<title>Sparrow Haulage — Business Card</title>
<link href="https://fonts.googleapis.com/css2?family=Arimo:wght@400;700&display=swap" rel="stylesheet">
<style>
  :root {
    --backdrop: #404040;
    --navy: #000056;
    --red: #b20606;
    --white: #ffffff;
  }
  * { margin: 0; padding: 0; box-sizing: border-box; }
  html, body {
    width: 1200px;
    height: 801px;
    overflow: hidden;
    background: var(--backdrop);
    font-family: "Arimo", Arial, sans-serif;
  }
  .card {
    position: absolute;
    top: 274px;
    width: 443px;
    height: 263px;
    overflow: hidden;
  }
  .card-front { left: 153px; background: var(--navy); }
  .card-back  { left: 625px; background: var(--white); }

  .front-panel {
    position: absolute;
    top: 0; right: 0;
    width: 113px; height: 100%;
    background: var(--white);
  }
  .front-band {
    position: absolute;
    top: 0; right: 70px;
    width: 28px; height: 100%;
    background: var(--red);
  }

  .holder-name {
    position: absolute;
    left: 19px; top: 30px;
    color: var(--red);
    font-weight: 700;
    font-size: 16.5px;
    letter-spacing: 0.1px;
  }
  .holder-title {
    position: absolute;
    left: 19px; top: 51px;
    color: var(--white);
    font-size: 12.5px;
  }
  .contact-list {
    position: absolute;
    left: 19px; top: 184px;
    list-style: none;
  }
  .contact-item {
    display: flex;
    align-items: center;
    height: 15.8px;
    color: var(--white);
    font-size: 12px;
  }
  .contact-icon {
    width: 11px; height: 11px;
    margin-right: 6px;
    flex: none;
  }

  .brand-lockup {
    position: absolute;
    left: 0; right: 0; top: 0; bottom: 0;
    display: flex;
    align-items: center;
    justify-content: center;
    gap: 12px;
  }
  .brand-mark {
    width: 26px; height: 26px;
    background: var(--red);
  }
  .brand-name {
    color: var(--navy);
    font-weight: 700;
    font-size: 22px;
    letter-spacing: 3px;
    text-transform: uppercase;
  }
</style>
</head>
<body>
  <section class="card card-front" aria-label="Business card front">
    <div class="front-panel"></div>
    <div class="front-band"></div>
    <h1 class="holder-name">MARTIN OBUYA</h1>
    <p class="holder-title">CEO/FOUNDER</p>
    <ul class="contact-list">
      <li class="contact-item">
        <svg class="contact-icon" viewBox="0 0 12 12" aria-hidden="true">
          <path d="M2.5 1 L4.5 1 L5.2 3.6 L4 4.5 C4.6 6 6 7.4 7.5 8 L8.4 6.8 L11 7.5 L11 9.5 C11 10.3 10.3 11 9.5 11 C5 11 1 7 1 2.5 C1 1.7 1.7 1 2.5 1 Z" fill="var(--red)"/>
        </svg>
        555-206-7142
      </li>
      <li class="contact-item">
        <svg class="contact-icon" viewBox="0 0 12 12" aria-hidden="true">
          <rect x="0.5" y="2" width="11" height="8" fill="var(--red)"/>
          <path d="M0.5 2 L6 6.5 L11.5 2 M0.5 10 L4.5 6 M11.5 10 L7.5 6" stroke="var(--navy)" stroke-width="0.8" fill="none"/>
        </svg>
        martinobuya@sparrow-haulage.example
      </li>
      <li class="contact-item">
        <svg class="contact-icon" viewBox="0 0 12 12" aria-hidden="true">
          <circle cx="6" cy="6" r="5" fill="none" stroke="var(--red)" stroke-width="1.1"/>
          <ellipse cx="6" cy="6" rx="2.2" ry="5" fill="none" stroke="var(--red)" stroke-width="0.9"/>
          <path d="M1 6 H11 M2 3.5 H10 M2 8.5 H10" stroke="var(--red)" stroke-width="0.9"/>
        </svg>
        www.sparrow-haulage.example
      </li>
    </ul>
  </section>

  <section class="card card-back" aria-label="Business card back">
    <div class="brand-lockup">
      <span class="brand-mark" aria-hidden="true"></span>
      <span class="brand-name">Sparrow Haulage</span>
    </div>
  </section>
</body>
</html>
```